QP Fiduciary Website Redesign Contest

We want to refresh our website to be more insitutional, professional for an international audience. We have designed a new logo for this purpose and that has been attached. A full brand brief and positioning statement has also been attached. Please read through all the documents carefully before designing. The old website is found here: https://qp-fiduciary.example/

Target Market(s)

Actuaries and associated businesses internationally

Industry/Entity Type

professional services - actuaries

Number of Pages Required

3 page

Font styles to use
Sans Serif

Colors
0054AA
0677BA
7BADD7
CADEEF
E8F1F8
0094D4
00A9DD
6FCCEA
C7EBF8
E9F6FB
F0912C
F2A743
F7CA91
FBE8D2
FDF5EE
EE7325
F08F49
F5BC92
FAE3D3
FDF4ED
EB3D1F
EC4F4E
F09395
F8D3D4
FCEDEE

Requirements
Must have
• blues and greens to match the logo color, complimentary colors, navigation
Nice to have
• old site: https://qp-fiduciary.example/

```html
<!DOCTYPE html>
<html lang="en">
<head>
<meta charset="utf-8">
<title>QP Fiduciary — Actuarial Software</title>
<link href="https://fonts.googleapis.com/css2?family=Audiowide&family=Roboto:wght@400;500;700&display=swap" rel="stylesheet">
<style>
:root{
  --navy:#1c4d93;
  --navy-dark:#0d2f63;
  --blue:#0677BA;
  --sky:#7BADD7;
  --pale:#E8F1F8;
  --panel:#dde9f4;
  --green:#1d9a7b;
  --teal:#4fc9a9;
  --cyan:#4ab0d9;
  --ink:#1b1b1b;
  --text:#333;
  --muted:#555;
  --line:#5a4ea6;
}
*{margin:0;padding:0;box-sizing:border-box}
html,body{width:1200px;height:4451px;overflow:hidden}
body{position:relative;background:#fff;font-family:"Roboto",Arial,sans-serif;color:var(--text)}
.abs{position:absolute}
.display{font-family:"Audiowide","Roboto",sans-serif;color:#111;text-transform:uppercase;letter-spacing:2px;font-weight:400}
.btn{position:absolute;display:flex;align-items:center;justify-content:center;gap:10px;border-radius:30px;background:var(--navy);color:#fff;font-weight:700;font-size:15px;text-transform:uppercase;text-decoration:none;letter-spacing:.2px}
.btn svg{width:26px;height:34px}
.btn.green{background:var(--green)}

/* hero */
.hero-bg{left:0;top:0;width:1200px;height:820px;background:
 radial-gradient(ellipse 520px 380px at 260px 80px,rgba(125,200,245,.9),transparent 70%),
 radial-gradient(ellipse 600px 500px at 900px 260px,rgba(130,190,250,.85),transparent 70%),
 radial-gradient(ellipse 500px 400px at 1100px 40px,rgba(190,230,250,.9),transparent 70%),
 linear-gradient(180deg,#cfe8fb 0%,#e9f4fd 60%,#fff 100%)}
.logo{left:143px;top:88px;font-size:38px;font-weight:700;color:var(--navy);letter-spacing:1px;display:flex;align-items:center;gap:12px}
.logo i{display:block;width:18px;height:18px;border-radius:50%;background:var(--green)}
.nav{left:541px;top:97px;display:flex;gap:32px;font-size:16px;font-weight:500;color:#1a1a1a}
.nav .active{position:relative}
.nav .active::after{content:"";position:absolute;left:0;right:0;bottom:-6px;height:3px;background:var(--green)}
.hero-title{left:143px;top:254px;font-size:31px;line-height:53px}
.hero-copy{left:143px;top:428px;width:560px;font-size:20px;line-height:35px;color:#222}

/* overview */
.section-title{left:0;width:1200px;text-align:center;font-size:34px}
.overview-copy{left:270px;top:932px;width:660px;text-align:center;font-size:20px;line-height:35px;color:#222}
.step{position:absolute;width:210px;text-align:center}
.step h3{font-size:21px;font-weight:500;color:#111;margin:8px 0 10px}
.step p{font-size:14px;line-height:19px;color:#444;width:166px;margin:0 auto}
.step svg{width:52px;height:52px}

/* solutions */
.sol-card{position:absolute;top:1751px;width:289px;height:331px;background:#fff;border-radius:8px;text-align:center;overflow:hidden}
.sol-card.featured{border:2px solid var(--green);box-shadow:0 8px 24px rgba(20,80,120,.15)}
.sol-card h3{font-size:19px;font-weight:700;color:#111;line-height:28px;margin-bottom:14px}
.sol-card p{font-size:14px;line-height:23px;color:#444;padding:0 34px}
.badge{position:absolute;left:82px;width:126px;height:126px;border-radius:50%;display:flex;justify-content:center}
.badge svg{width:44px;height:44px}
.circ-arrow{display:inline-block;margin-top:22px;width:32px;height:32px}

/* characteristics */
.trait{position:absolute;top:2524px;width:210px;height:210px;border-radius:50%;display:flex;flex-direction:column;align-items:center;justify-content:center;color:#fff;text-align:center;font-size:16px;line-height:24px;font-weight:500;padding:0 26px}
.trait svg{width:50px;height:50px;margin-bottom:14px}

/* insights */
.post{position:absolute;top:3195px;width:289px;height:327px;border-radius:6px;overflow:hidden;display:flex;flex-direction:column;align-items:center;justify-content:center;text-align:center;color:#fff}
.post h3{font-size:22px;line-height:28px;font-weight:700;padding:0 36px}
.post a{margin-top:14px;color:#2fc29a;font-size:14px;text-decoration:underline}

/* cta */
.cta-title{left:0;width:1200px;top:3820px;text-align:center;font-size:33px;line-height:54px;color:#fff}

/* footer */
.foot-nav{left:0;width:1200px;top:4202px;display:flex;justify-content:center;gap:22px;font-size:18px;font-weight:500;color:#111}
.foot-contact{left:0;width:1200px;top:4256px;display:flex;justify-content:center;align-items:center;gap:12px;font-size:17px;color:#111}
.foot-contact svg{width:16px;height:16px}
.foot-legal{left:0;width:1200px;top:4309px;text-align:center;font-size:16px;color:#111}
.social{left:580px;top:4361px;width:40px;height:40px;border-radius:50%;background:var(--navy)}
</style>
</head>
<body>

<!-- HERO -->
<div class="abs hero-bg"></div>
<a class="btn" href="#" style="left:690px;top:21px;width:365px;height:50px">Request a technical walkthrough
<svg viewBox="0 0 26 34"><path d="M6 32 Q24 24 18 2" stroke="#fff" stroke-width="2" fill="none"/></svg></a>
<div class="abs logo"><i></i>QP FIDUCIARY</div>
<nav class="abs nav">
  <span class="active">Home</span><span>Platform</span><span>Solutions</span><span>Insights</span><span>Company</span><span>Contact</span>
</nav>
<h1 class="abs display hero-title">Actuarial software for<br>structured, auditable<br>financial analysis</h1>
<p class="abs hero-copy">Software that translates actuarial methodologies into disciplined decision-ready analytical tools across diverse regulatory environments.</p>
<a class="btn" href="#" style="left:143px;top:564px;width:365px;height:50px">Request a technical walkthrough
<svg viewBox="0 0 26 34"><path d="M6 32 Q24 24 18 2" stroke="#fff" stroke-width="2" fill="none"/></svg></a>
<svg class="abs" style="left:586px;top:724px" width="28" height="66" viewBox="0 0 28 66">
  <rect x="3" y="2" width="22" height="36" rx="11" fill="none" stroke="#222" stroke-width="2"/>
  <line x1="14" y1="9" x2="14" y2="16" stroke="#222" stroke-width="2"/>
  <path d="M6 46 L14 53 L22 46 M6 55 L14 62 L22 55" fill="none" stroke="#222" stroke-width="2"/>
</svg>

<!-- PLATFORM OVERVIEW -->
<h2 class="abs display section-title" style="top:862px">Platform overview</h2>
<p class="abs overview-copy">QP Fiduciary develops modular actuarial software designed to support reserving, valuation, pricing, and risk analysis workflows across diverse regulatory environments.</p>

<svg class="abs" style="left:150px;top:1100px" width="900" height="180" viewBox="0 0 900 180">
  <g fill="none" stroke="var(--line)" stroke-width="2">
    <path d="M14 100 V135 Q14 162 41 162 H203 Q230 162 230 135 V100"/>
    <path d="M230 100 V38 Q230 11 257 11 H423 Q450 11 450 38 V100"/>
    <path d="M450 100 V135 Q450 162 477 162 H643 Q670 162 670 135 V100"/>
    <path d="M670 100 V38 Q670 11 697 11 H860 Q887 11 887 38 V90"/>
  </g>
  <circle cx="14" cy="100" r="9" fill="var(--green)"/>
  <circle cx="230" cy="100" r="9" fill="var(--navy)"/>
  <circle cx="450" cy="100" r="9" fill="var(--green)"/>
  <circle cx="670" cy="100" r="9" fill="var(--navy)"/>
  <path d="M878 90 H896 L887 106 Z" fill="var(--green)"/>
</svg>

<div class="step" style="left:168px;top:1106px">
  <svg viewBox="0 0 52 52" fill="none" stroke="var(--navy)" stroke-width="2"><rect x="6" y="9" width="40" height="36" rx="3"/><line x1="6" y1="18" x2="46" y2="18"/><line x1="16" y1="4" x2="16" y2="12"/><line x1="36" y1="4" x2="36" y2="12"/><g fill="var(--navy)" stroke="none"><rect x="12" y="24" width="5" height="5"/><rect x="23" y="24" width="5" height="5"/><rect x="34" y="24" width="5" height="5"/><rect x="12" y="34" width="5" height="5"/><rect x="23" y="34" width="5" height="5"/></g></svg>
  <h3>Reserving</h3><p>Nemo enim ipsam voluptatem quia voluptas sit aspernatur aut</p>
</div>
<div class="step" style="left:386px;top:1136px">
  <svg viewBox="0 0 52 52" fill="none" stroke="var(--green)" stroke-width="2"><rect x="8" y="6" width="30" height="40" rx="2"/><circle cx="23" cy="20" r="7"/><line x1="14" y1="34" x2="32" y2="34"/><line x1="14" y1="40" x2="28" y2="40"/><path d="M38 14 L46 10 V44 L38 46"/></svg>
  <h3>Valuation</h3><p>Nemo enim ipsam voluptatem quia voluptas sit aspernatur aut</p>
</div>
<div class="step" style="left:607px;top:1106px">
  <svg viewBox="0 0 52 52" fill="none" stroke="var(--navy)" stroke-width="2"><path d="M10 30 L26 8 L42 22 L28 46 Z"/><circle cx="30" cy="18" r="3"/><circle cx="24" cy="31" r="6"/></svg>
  <h3>Pricing</h3><p>Nemo enim ipsam voluptatem quia voluptas sit aspernatur aut</p>
</div>
<div class="step" style="left:826px;top:1136px">
  <svg viewBox="0 0 52 52" fill="none" stroke="var(--green)" stroke-width="2"><path d="M20 6 L36 34 H4 Z"/><line x1="20" y1="16" x2="20" y2="26"/><circle cx="20" cy="30" r="1" fill="var(--green)"/><circle cx="34" cy="32" r="9"/><line x1="40" y1="39" x2="47" y2="46"/></svg>
  <h3>Risk Analysis</h3><p>Nemo enim ipsam voluptatem quia voluptas sit aspernatur aut</p>
</div>

<a class="btn" href="#" style="left:417px;top:1380px;width:366px;height:50px">Request a technical walkthrough
<svg viewBox="0 0 26 34"><path d="M6 32 Q24 24 18 2" stroke="#fff" stroke-width="2" fill="none"/></svg></a>

<!-- CORE SOLUTIONS -->
<svg class="abs" style="left:0;top:1480px" width="1200" height="790" viewBox="0 0 1200 790">
  <path d="M54 96 L1140 12 Q1176 10 1176 46 V740 Q1176 776 1140 772 L60 688 Q24 686 24 650 V130 Q24 98 54 96 Z" fill="var(--panel)"/>
</svg>
<h2 class="abs display section-title" style="top:1655px">Core solutions</h2>

<div class="sol-card" style="left:145px">
  <div class="badge" style="top:-64px;background:var(--navy);align-items:flex-end;padding-bottom:18px">
    <svg viewBox="0 0 44 44" fill="none" stroke="#fff" stroke-width="2"><rect x="6" y="6" width="22" height="30" rx="2"/><line x1="11" y1="14" x2="23" y2="14"/><line x1="11" y1="20" x2="23" y2="20"/><circle cx="30" cy="30" r="8"/></svg>
  </div>
  <div style="padding-top:90px">
    <h3>RESERVING &amp;<br>VALUATION</h3>
    <p>Software supporting structured reserving workflows and financial reporting across jurisdictions.</p>
    <svg class="circ-arrow" viewBox="0 0 32 32" fill="none" stroke="var(--navy)" stroke-width="2"><circle cx="16" cy="16" r="14"/><path d="M13 9 L20 16 L13 23"/></svg>
  </div>
</div>
<div class="sol-card featured" style="left:456px">
  <div style="padding-top:40px">
    <h3>PRICING</h3>
    <p>Models supporting insurance and reinsurance pricing based on actuarial methodologies.</p>
    <svg class="circ-arrow" viewBox="0 0 32 32" fill="none" stroke="var(--navy)" stroke-width="2"><circle cx="16" cy="16" r="14"/><path d="M13 9 L20 16 L13 23"/></svg>
  </div>
  <div class="badge" style="top:252px;left:80px;background:var(--green);align-items:flex-start;padding-top:16px">
    <svg viewBox="0 0 44 44" fill="none" stroke="#fff" stroke-width="2"><circle cx="26" cy="14" r="9"/><path d="M26 9 V19 M23 12 H29 M23 16 H29"/><path d="M4 40 V28 L14 26 L24 32 H34"/></svg>
  </div>
</div>
<div class="sol-card" style="left:764px">
  <div class="badge" style="top:-64px;background:var(--navy);align-items:flex-end;padding-bottom:18px">
    <svg viewBox="0 0 44 44" fill="none" stroke="#fff" stroke-width="2"><rect x="6" y="8" width="18" height="30"/><rect x="24" y="16" width="12" height="22"/><line x1="11" y1="14" x2="19" y2="14"/><line x1="11" y1="22" x2="19" y2="22"/><line x1="11" y1="30" x2="19" y2="30"/><circle cx="34" cy="12" r="6"/></svg>
  </div>
  <div style="padding-top:90px">
    <h3>ENTERPRISE RISK<br>MANAGEMENT</h3>
    <p>Software supporting reinsurance optimization and capital modeling.</p>
    <svg class="circ-arrow" viewBox="0 0 32 32" fill="none" stroke="var(--navy)" stroke-width="2" style="margin-top:36px"><circle cx="16" cy="16" r="14"/><path d="M13 9 L20 16 L13 23"/></svg>
  </div>
</div>

<!-- PLATFORM CHARACTERISTICS -->
<h2 class="abs display section-title" style="top:2364px">Platform characteristics</h2>
<div class="abs" role="img" aria-label="Flowing wave lines decoration" style="left:0;top:2500px;width:1200px;height:560px;background:
 radial-gradient(ellipse 700px 140px at 500px 220px,rgba(123,173,215,.35),transparent 70%),
 radial-gradient(ellipse 500px 120px at 650px 420px,rgba(123,173,215,.28),transparent 70%),
 radial-gradient(ellipse 400px 90px at 1050px 120px,rgba(111,204,180,.25),transparent 70%)"></div>
<svg class="abs" style="left:0;top:2480px" width="1200" height="300" viewBox="0 0 1200 300">
  <g fill="none" stroke="var(--navy)" stroke-width="3">
    <path d="M364 195 A115 115 0 0 0 482 278"/>
    <path d="M830 195 A115 115 0 0 0 950 278"/>
  </g>
  <path d="M597 120 A115 115 0 0 1 716 20" fill="none" stroke="var(--green)" stroke-width="3"/>
  <circle cx="482" cy="278" r="6" fill="var(--navy)"/>
  <circle cx="716" cy="20" r="6" fill="var(--green)"/>
  <circle cx="950" cy="278" r="6" fill="var(--navy)"/>
</svg>
<div class="trait" style="left:145px;background:#2a80c8">
  <svg viewBox="0 0 50 50" fill="none" stroke="#fff" stroke-width="2"><circle cx="25" cy="16" r="6"/><path d="M14 32 Q25 20 36 32"/><circle cx="10" cy="22" r="4"/><circle cx="40" cy="22" r="4"/><path d="M8 44 H42"/></svg>
  Structured Workflows Suitable for Multi Jurisdictional Review
</div>
<div class="trait" style="left:377px;background:var(--green)">
  <svg viewBox="0 0 50 50" fill="none" stroke="#fff" stroke-width="2"><rect x="8" y="8" width="26" height="34"/><circle cx="30" cy="26" r="9"/><line x1="36" y1="33" x2="44" y2="41"/></svg>
  Transparent Assumptions &amp; Methodological Clarity
</div>
<div class="trait" style="left:611px;background:var(--cyan)">
  <svg viewBox="0 0 50 50" fill="none" stroke="#fff" stroke-width="2"><path d="M6 10 H22 V34 H6 Z M28 10 H44 V34 H28 Z"/><circle cx="25" cy="30" r="5"/><line x1="25" y1="35" x2="25" y2="44"/></svg>
  Comparative Scenario Analysis
</div>
<div class="trait" style="left:844px;background:var(--teal)">
  <svg viewBox="0 0 50 50" fill="none" stroke="#fff" stroke-width="2"><circle cx="30" cy="16" r="8"/><circle cx="30" cy="16" r="3"/><path d="M4 40 V30 L16 28 L26 34 H40"/></svg>
  Supports Professional Judgment Rather Than Replacing It
</div>

<!-- INSIGHTS -->
<h2 class="abs display section-title" style="top:3100px">Insights</h2>
<div class="post" role="img" aria-label="Abstract digital particle background" style="left:145px;background:radial-gradient(circle at 30% 30%,#6b3fd0 0%,#3a2aa0 30%,#10174a 75%)">
  <h3 style="margin-top:60px">Methodological Perspectives in Actuarial Reserving</h3><a href="#">READ MORE</a>
</div>
<div class="post" role="img" aria-label="Dark blue technology background" style="left:456px;background:linear-gradient(160deg,#1c3d86,#0d1f4f);border:2px solid #0d1f4f">
  <div style="position:absolute;inset:14px;border:1px solid rgba(255,255,255,.25);border-radius:6px"></div>
  <h3 style="margin-top:-20px">Governance Considerations in Multi-Jurisdictional Analysis</h3><a href="#">READ MORE</a>
</div>
<div class="post" role="img" aria-label="Network connections background" style="left:764px;background:radial-gradient(circle at 60% 70%,#1f5fa0 0%,#0e2d66 50%,#081a40 100%)">
  <h3 style="margin-top:40px">Observations on Actuarial Practice in Emerging Markets</h3><a href="#">READ MORE</a>
</div>
<a class="btn" href="#" style="left:489px;top:3577px;width:220px;height:52px">Read insights
<svg viewBox="0 0 26 34"><path d="M6 32 Q24 24 18 2" stroke="#fff" stroke-width="2" fill="none"/></svg></a>

<!-- CTA -->
<svg class="abs" style="left:0;top:3680px" width="1200" height="490" viewBox="0 0 1200 490" role="img" aria-label="Deep blue abstract background">
  <defs><linearGradient id="ctaGrad" x1="0" y1="1" x2="1" y2="0"><stop offset="0" stop-color="#0a2458"/><stop offset=".6" stop-color="#123f86"/><stop offset="1" stop-color="#2a78c2"/></linearGradient></defs>
  <path d="M60 92 L1140 8 Q1176 6 1176 42 V440 Q1176 478 1140 474 L60 390 Q24 388 24 352 V128 Q24 94 60 92 Z" fill="url(#ctaGrad)"/>
</svg>
<h2 class="abs display cta-title">Interested in exploring<br>the platform?</h2>
<a class="btn green" href="#" style="left:417px;top:3959px;width:366px;height:50px">Request a technical walkthrough
<svg viewBox="0 0 26 34"><path d="M6 32 Q24 24 18 2" stroke="#fff" stroke-width="2" fill="none"/></svg></a>

<!-- FOOTER -->
<nav class="abs foot-nav"><span>COMPANY</span><span>/</span><span>PLATFORM</span><span>/</span><span>SOLUTIONS</span><span>/</span><span>INSIGHTS</span><span>/</span><span>CONTACT</span></nav>
<div class="abs foot-contact">
  <svg viewBox="0 0 16 16"><path d="M3 1 L6 1 L7 5 L5 6 Q6 9 10 11 L11 9 L15 10 L15 13 Q14 15 12 15 Q2 13 1 3 Q1 1 3 1 Z" fill="var(--green)"/></svg>
  <span>+1 888 888 8888</span><span>|</span>
  <svg viewBox="0 0 16 16"><rect x="1" y="3" width="14" height="10" fill="var(--green)"/><path d="M1 3 L8 9 L15 3" fill="none" stroke="#fff" stroke-width="1.4"/></svg>
  <span>info@companyname.com</span>
</div>
<p class="abs foot-legal">© 2026 Companyname.All Rights Reserved &nbsp;|&nbsp; Privacy Policy &nbsp;|&nbsp; Terms of use &nbsp;|&nbsp; Legal</p>
<div class="abs social" aria-label="Social profile"></div>

</body>
</html>
```